ELsewhen website redesign to provide information about experiential workshops, film work and other

We need a redesign of our website elsewhen.org. We conduct experiential workshops of discovery and transformation for individuals and organizations. We need the website to reflect the full extent of ELsewhen programs, and be an information hub for ELsewhen workshops and communities as they develop.

The attached documents contain information about the organization - it's brandbook, copy for web pages, a website layout and a couple of images.

The site is for individuals and companies looking to promote and be change to make a difference. It should be warm, welcoming, and create excitement around the concepts and the ability to discover a new way of being in the world. We are about creating communities around the globe who will embody play, freedom, curiosity and expanded possibilities. We are creating a space for this to happen, both physically (workshops) and online.

We will be on either a SquareSpace, but mos tlikely a Weebly plaform.

Please look at the current site at www.elsewhen.org

Target Market(s)

Initially, are target market will be baby boomers, but will expand to include millennials and students.

Coding

Coded - Design and coding required

Number of Pages Required

5+ page

Requirements
Must have
• The colors, logo and fonts from the brand book.
Nice to have
• Complimentary use of brand colors to create an attractive presentation and energy

```html
<!DOCTYPE html>
<html lang="en">
<head>
<meta charset="utf-8">
<title>ELsewhen — Home</title>
<link href="https://fonts.googleapis.com/css2?family=Lato:wght@400;700;900&display=swap" rel="stylesheet">
<style>
:root{
  --ink:#1f1f1f;
  --page:#ffffff;
  --field:#e6e6e6;
  --panel:#232323;
  --footer:#262626;
  --maroon:#7a5560;
  --maroon-text:#d9c9cc;
  --orange:#f3a43a;
  --rust:#e05a2c;
  --green:#5f9e6c;
  --teal:#86b8bd;
  --moss:#6b9a6a;
  --gold:#dca242;
  --ember:#d0582c;
  --symbol:#c9c9c9;
  --dim:rgba(0,0,0,.2);
}
*{margin:0;padding:0;box-sizing:border-box}
html,body{width:1200px;height:3232px;overflow:hidden}
body{position:relative;background:var(--page);font-family:'Lato',sans-serif;color:var(--ink)}
.abs{position:absolute}
.center-x{transform:translateX(-50%);white-space:nowrap}

/* header & hero */
.hero{left:0;top:0;width:1200px;height:668px;background:linear-gradient(160deg,#4a3a2e 0%,#6e5a47 35%,#3c3129 70%,#2a2420 100%)}
.brand{font-family:'Lato',sans-serif;font-weight:900;letter-spacing:3px;color:#fff;line-height:1;white-space:nowrap}
.header-brand{left:75px;top:36px;font-size:34px}
.btn{display:flex;align-items:center;justify-content:center;color:#fff;font-size:15px;font-weight:700;letter-spacing:.5px;border-radius:2px}
.btn-capture{left:786px;top:32px;width:158px;height:39px;background:var(--green)}
.btn-login{left:961px;top:32px;width:163px;height:39px;background:var(--orange)}
.nav-rule{left:75px;width:1050px;height:1px;background:rgba(255,255,255,.35)}
.nav a{position:absolute;top:121px;color:#fff;font-size:14px;text-decoration:none;letter-spacing:.4px;transform:translateX(-50%);white-space:nowrap}

.question{top:569px;height:194px;width:524px;background:var(--panel);color:#e8e8e8;text-align:center;padding-top:36px}
.question h2{font-size:33px;font-weight:700;line-height:37px;letter-spacing:.5px}
.question svg{margin-top:16px}

/* discover */
.discover-title{left:0;width:1200px;top:812px;text-align:center;font-size:26px;font-weight:700;line-height:32px}
.discover-brand{color:var(--ink);font-size:34px;left:600px;top:912px}
.node{width:86px;height:86px;border-radius:50%;display:flex;align-items:center;justify-content:center}
.node-label{font-size:16px;font-weight:700;text-align:center;line-height:23px;width:240px;transform:translateX(-50%);color:#333}

/* vision */
.vision{left:0;top:1271px;width:616px;height:381px;background:var(--maroon);padding:42px 75px 0}
.section-head{font-size:26px;letter-spacing:1px;color:#eee;font-weight:400}
.vision p,.calm p{color:var(--maroon-text);font-size:14px;line-height:26px;margin-top:14px}
.photo-vision{left:616px;top:1271px;width:584px;height:381px;background:linear-gradient(135deg,#2f4a2c 0%,#54704a 40%,#3a2f2a 75%,#1f1d1b 100%)}

/* what we do */
.h-section{left:0;width:1200px;text-align:center;font-size:27px;font-weight:700}
.accent{color:var(--rust);font-weight:700}
.wwd-sub{left:0;width:1200px;top:1768px;text-align:center;font-size:14px}
.wwd-body{left:80px;width:1040px;top:1794px;text-align:center;font-size:14px;line-height:27px;color:#333}
.wwd-line{left:0;width:1200px;top:1898px;text-align:center;font-size:14px;color:#333}
.movement{width:200px;transform:translateX(-50%);text-align:center;top:1955px}
.symbol{width:96px;height:96px;margin:0 auto;background:var(--symbol)}
.movement span{display:block;margin-top:22px;font-size:16px;font-weight:700;color:#333}

/* calm */
.photo-calm{left:0;top:2158px;width:586px;height:405px;background:linear-gradient(170deg,#3b3b38 0%,#5d5a52 40%,#2e2c28 80%,#1c1b19 100%)}
.calm{left:586px;top:2158px;width:614px;height:405px;background:var(--maroon);padding:47px 28px 0 28px}
.calm p{line-height:25px;margin-top:16px}

/* community form */
.community-text{left:0;width:1200px;top:2670px;text-align:center;font-size:14px;line-height:26px;color:#333}
.field{background:var(--field);border:1px solid #d8d8d8;font-size:13px;letter-spacing:.5px;color:#555;padding:0 15px;display:flex;align-items:center}
.field-msg{align-items:flex-start;padding-top:18px}
.btn-send{left:614px;top:2886px;width:422px;height:54px;background:var(--rust)}

/* footer */
.footer{left:0;top:2992px;width:1200px;height:240px;background:var(--footer)}
.footer-brand{left:75px;top:3070px;font-size:28px;color:#e0e0e0}
.foot-small{color:#8a8a8a;font-size:12px;line-height:26px}
.foot-head{color:#e0e0e0;font-size:14px;font-weight:700;letter-spacing:.6px}
.foot-link{color:#9a9a9a;font-size:13px;line-height:30px}
.foot-input{left:657px;top:3065px;width:226px;height:39px;background:#3a3a3a;color:#888;font-size:13px;padding-left:14px;display:flex;align-items:center}
.btn-signup{left:803px;top:3115px;width:80px;height:36px;background:var(--green);font-size:13px}
.social{width:22px;height:22px;border-radius:50%;background:#9a9a9a;top:3066px}

/* dim & modal */
.dim{left:0;top:0;width:1200px;height:3232px;background:var(--dim)}
.modal{left:254px;top:134px;width:692px;height:228px;background:#fff}
.modal h2{position:absolute;left:0;width:692px;top:29px;text-align:center;font-size:31px;font-weight:700;letter-spacing:1px}
.modal .close{position:absolute;left:665px;top:4px;font-size:20px;font-weight:900}
.modal .input{position:absolute;top:81px;width:196px;height:43px;border:1px solid #bbb;font-size:14px;color:#555;padding-left:10px;display:flex;align-items:center}
.modal .btn-register{position:absolute;left:196px;top:142px;width:302px;height:41px;background:var(--orange);font-size:17px}
</style>
</head>
<body>

<header>
  <div class="abs hero" role="img" aria-label="Workshop participants seated together in a warm wooden room"></div>
  <div class="abs brand header-brand">ELSEWHEN</div>
  <div class="abs btn btn-capture">EMAIL CAPTURE</div>
  <div class="abs btn btn-login">MEMBER LOGIN</div>
  <div class="abs nav-rule" style="top:103px"></div>
  <nav class="nav">
    <a style="left:116px">HOME</a>
    <a style="left:213px">ABOUT US</a>
    <a style="left:334px">WORKSHOPS</a>
    <a style="left:500px">ELSEWHEN PROJECTS</a>
    <a style="left:642px">FILMS</a>
    <a style="left:773px">STORE &amp; RESOURCES</a>
    <a style="left:930px">COMMUNITY</a>
    <a style="left:1060px">CONTACT US</a>
  </nav>
  <div class="abs nav-rule" style="top:155px"></div>

  <div class="abs question" style="left:75px">
    <h2>WHAT WORLD DO WE<br>WANT TO LIVE IN?</h2>
    <svg width="30" height="28" viewBox="0 0 30 28"><path d="M2 14H24M14 4L25 14L14 24" fill="none" stroke="#f3a43a" stroke-width="5"/></svg>
  </div>
  <div class="abs question" style="left:601px">
    <h2>WHAT KIND OF LIFE DO YOU<br>WANT TO CREATE?</h2>
    <svg width="30" height="28" viewBox="0 0 30 28"><path d="M2 14H24M14 4L25 14L14 24" fill="none" stroke="#f3a43a" stroke-width="5"/></svg>
  </div>
</header>

<section class="discover">
  <h2 class="abs discover-title">DISCOVER AN OPPORTUNITY TO LIVE A MORE DYNAMIC<br>AND MEANINGFUL LIFE</h2>
  <div class="abs brand discover-brand center-x">ELSEWHEN</div>
  <svg class="abs" style="left:0;top:980px" width="1200" height="170" viewBox="0 980 1200 170">
    <path d="M172 1030 Q280 1110 386 1096 Q500 1080 599 1030 Q710 1090 814 1096 Q920 1090 1027 1030" fill="none" stroke="#555" stroke-width="2" stroke-dasharray="3 5"/>
  </svg>
  <div class="abs node" style="left:129px;top:987px;background:var(--moss)">
    <svg width="40" height="40" viewBox="0 0 40 40"><path d="M20 4L30 18H25L33 30H7L15 18H10Z" fill="#fff"/><rect x="18" y="30" width="4" height="6" fill="#fff"/></svg>
  </div>
  <div class="abs node" style="left:343px;top:1053px;background:var(--gold)">
    <svg width="44" height="34" viewBox="0 0 44 34"><circle cx="22" cy="9" r="6" fill="#fff"/><circle cx="9" cy="13" r="5" fill="#fff"/><circle cx="35" cy="13" r="5" fill="#fff"/><path d="M12 32Q22 14 32 32Z M1 32Q9 18 17 32Z M27 32Q35 18 43 32Z" fill="#fff"/></svg>
  </div>
  <div class="abs node" style="left:556px;top:987px;background:var(--teal)">
    <svg width="42" height="36" viewBox="0 0 42 36"><ellipse cx="20" cy="15" rx="18" ry="12" fill="#fff"/><path d="M8 24L5 34L17 26Z" fill="#fff"/></svg>
  </div>
  <div class="abs node" style="left:771px;top:1053px;background:var(--ember)">
    <svg width="30" height="40" viewBox="0 0 30 40"><circle cx="15" cy="6" r="5" fill="#fff"/><path d="M3 10L15 18L27 10L24 8L15 13L6 8Z M11 17H19V38H11Z" fill="#fff"/></svg>
  </div>
  <div class="abs node" style="left:984px;top:987px;background:#222">
    <svg width="28" height="40" viewBox="0 0 28 40"><path d="M14 3A11 11 0 0 1 20 23V28H8V23A11 11 0 0 1 14 3Z" fill="none" stroke="#fff" stroke-width="3"/><path d="M9 32H19M10 36H18" stroke="#fff" stroke-width="3"/></svg>
  </div>
  <div class="abs node-label" style="left:172px;top:1087px">Moves Energy</div>
  <div class="abs node-label" style="left:386px;top:1156px">Creates Opportunities<br>for Connecting</div>
  <div class="abs node-label" style="left:599px;top:1087px">Supports Conscious<br>Evolution</div>
  <div class="abs node-label" style="left:814px;top:1156px">Deepens Experience<br>of Life</div>
  <div class="abs node-label" style="left:1027px;top:1087px">Provides Opportunities for<br>Collaboration &amp; Creation</div>
</section>

<section>
  <div class="abs vision">
    <h2 class="section-head">VISION</h2>
    <p>We envision a world in which all people and communities can challenge and break free from stories that no longer serve us. We believe that solutions to contemporary challenges will emerge from a place of curiosity, love and connection.</p>
    <p>Through inspiration, conscious reflection, and collaboration, we take responsibility for the world we are manifesting, and we can discover and create new possibilities for the lives and the society we desire to build.</p>
  </div>
  <div class="abs photo-vision" role="img" aria-label="Two workshop facilitators seated in a bright room with forest windows"></div>
</section>

<section>
  <h2 class="abs h-section" style="top:1709px">WHAT WE DO</h2>
  <div class="abs wwd-sub accent">ELSEWHEN LIFE:</div>
  <p class="abs wwd-body">Elsewhen Life is a workshop designed to re-engage you with life. Through interactive exercises and personal exploration, you are taken on a journey that ultimately leaves you experiencing life as a Creator. You will learn to see beliefs and patterns that hold you back in work and relationships as well as a path to transforming the story of your life.</p>
  <p class="abs wwd-line"><span class="accent">ELSEWHEN LIFE</span> IS A 2-3 DAY WORKSHOP EXPERIENCED IN 5 MOVEMENTS:</p>
  <div class="abs movement" style="left:172px">
    <div class="symbol" role="img" aria-label="Line symbol for the Curiosity movement"></div>
    <span>Curiosity</span>
  </div>
  <div class="abs movement" style="left:386px">
    <div class="symbol" role="img" aria-label="Line symbol for the Awareness movement"></div>
    <span>Awareness</span>
  </div>
  <div class="abs movement" style="left:601px">
    <div class="symbol" role="img" aria-label="Line symbol for the Owning the Creation movement"></div>
    <span>Owning the Creation</span>
  </div>
  <div class="abs movement" style="left:814px">
    <div class="symbol" role="img" aria-label="Line symbol for the Reimagining movement"></div>
    <span>Reimagining</span>
  </div>
  <div class="abs movement" style="left:1027px">
    <div class="symbol" role="img" aria-label="Line symbol for the Manifesting movement"></div>
    <span>Manifesting</span>
  </div>
</section>

<section>
  <div class="abs photo-calm" role="img" aria-label="Costumed performers gathered outdoors in front of a weathered barn"></div>
  <div class="abs calm">
    <h2 class="section-head">UNSETTLING THE CALM</h2>
    <p>The Unsettling the Calm workshop—an extension of the documentary of the same name—is an experiential process to transform participants into disturbers of the status quo within themselves, to enhance their relationships with others, and to change the environments in which they exist—and ultimately society—for the better.</p>
    <p>This workshop experience challenges us all to understand the narratives we live within, to look at our current roles in society, and to decide what role we will play to create a more humane, just and peaceful world, for all. It all starts with our willingness to disturb the "calm" of the status quo.</p>
  </div>
</section>

<section>
  <h2 class="abs h-section" style="top:2614px">IN YOUR COMMUNITY</h2>
  <p class="abs community-text">Bring Elsewhen or the Unsettling the Calm workshop to your community. We would love to hear from you.<br>Please fill out the brief form here</p>
  <div class="abs field" style="left:164px;top:2753px;width:422px;height:54px">NAME</div>
  <div class="abs field" style="left:164px;top:2820px;width:422px;height:54px">EMAIL ADDRESS</div>
  <div class="abs field" style="left:164px;top:2886px;width:422px;height:54px">PHONE NO</div>
  <div class="abs field field-msg" style="left:614px;top:2753px;width:422px;height:121px">MESSAGE</div>
  <div class="abs btn btn-send">SUBMIT NOW</div>
</section>

<footer>
  <div class="abs footer"></div>
  <div class="abs brand footer-brand">ELSEWHEN</div>
  <div class="abs foot-small" style="left:75px;top:3110px">Copyright © 2018. Elsewhen Collective<br>All Right Reserved</div>
  <div class="abs foot-head" style="left:342px;top:3031px">SITE MAP</div>
  <div class="abs foot-link" style="left:342px;top:3052px">About Us<br>Workshops<br>Elsewhen Projects<br>Films</div>
  <div class="abs foot-link" style="left:508px;top:3052px">Store &amp; Resources<br>Community<br>Contact Us</div>
  <div class="abs foot-head" style="left:657px;top:3031px">EMAIL SIGN UP</div>
  <div class="abs foot-input">Enter Email Address</div>
  <div class="abs btn btn-signup">SIGN UP</div>
  <div class="abs foot-head" style="left:926px;top:3031px">FOLLOW US</div>
  <div class="abs social" style="left:922px"></div>
  <div class="abs social" style="left:957px"></div>
  <div class="abs social" style="left:992px"></div>
  <div class="abs social" style="left:1027px"></div>
  <div class="abs social" style="left:1062px"></div>
  <div class="abs social" style="left:1097px"></div>
</footer>

<div class="abs dim"></div>
<div class="abs modal" role="dialog" aria-label="Register">
  <span class="close">x</span>
  <h2>REGISTER</h2>
  <div class="input" style="left:41px">First Name</div>
  <div class="input" style="left:248px">Last Name</div>
  <div class="input" style="left:457px">Email Address</div>
  <div class="btn btn-register">SUBMIT</div>
</div>

</body>
</html>
```